Letterhead and matching envelope design for a dental office

We need a new stationary design, letterhead and envelope #10, for a dental office in Denver area. We are called Bright Harbor Dental. We want a simple and minimalistic design but not a boring design. I wish to have one good point that makes it look professional. I have attached our logo. Feel free to use either one. I want the design for letterhead and envelope look like a "matching pair" but not look the same. The envelope doesn't have to be white and it will have an address window on bottom left.

Target Market(s)

everyone who visits dentist (adults)

Industry/Entity Type

Dental

Font styles to use
Other font styles liked:
• close to font on logo or something that matches well

Requirements
Must have
• professional
• simple, minimalistic
• unique point that stands out
Nice to have
• matching but not same design for letterhead and envelope
Should not have
• not look like all the other boring designs
• no flowery, distracting feats

```html
<!DOCTYPE html>
<html lang="en">
<head>
<meta charset="utf-8">
<title>Bright Harbor Dental — Letterhead and Envelope</title>
<link rel="stylesheet" href="https://fonts.googleapis.com/css2?family=Cinzel:wght@600&family=Open+Sans:wght@400;600&display=swap">
<style>
  :root {
    --backdrop: #1d6b4f;
    --paper: #f7f8f7;
    --paper-shade: #eceeed;
    --brand-green: #1f8f3a;
    --brand-green-dark: #157a30;
    --swoosh: #e3e5e4;
    --swoosh-dark: #d6d9d8;
    --ink: #4a4f4d;
    --ink-soft: #8a8f8d;
  }
  * { box-sizing: border-box; margin: 0; padding: 0; }
  html, body { width: 1200px; height: 891px; overflow: hidden; }
  body {
    background: var(--backdrop);
    font-family: "Open Sans", sans-serif;
    position: relative;
  }
  .brand-name {
    font-family: "Cinzel", serif;
    font-weight: 600;
    color: var(--brand-green);
    letter-spacing: 0.06em;
    white-space: nowrap;
  }
  .brand-mark { display: flex; align-items: center; gap: 8px; }
  .brand-dot {
    width: 12px; height: 12px; border-radius: 50%;
    background: var(--brand-green);
  }

  /* Letterhead */
  .letterhead {
    position: absolute; left: 70px; top: 118px;
    width: 460px; height: 650px;
    background: var(--paper);
    box-shadow: 0 10px 24px rgba(0,0,0,0.25);
    overflow: hidden;
  }
  .letterhead .swooshes { position: absolute; inset: 0; }
  .letterhead .brand-mark { position: absolute; left: 34px; top: 132px; }
  .letterhead .brand-mark .brand-name { font-size: 17px; }
  .letterhead-contact {
    position: absolute; right: 30px; top: 30px;
    text-align: right; font-size: 8.5px; line-height: 1.6; color: var(--ink);
  }
  .letterhead-contact .brand-name { font-size: 14px; display: block; margin-bottom: 3px; }
  .letterhead-contact .provider { font-weight: 600; }
  .services {
    position: absolute; left: 34px; right: 30px; bottom: 30px;
    font-size: 9px; color: var(--ink-soft); line-height: 1.9;
  }
  .services-title {
    display: inline-block; font-weight: 600; color: var(--ink);
    border-left: 1px solid var(--ink); border-right: 1px solid var(--ink);
    padding: 0 6px; margin-bottom: 2px;
  }
  .services ul { list-style: none; display: flex; flex-wrap: wrap; gap: 0 12px; }
  .services li::before {
    content: ""; display: inline-block; margin-right: 4px;
    border-left: 5px solid var(--brand-green);
    border-top: 3.5px solid transparent; border-bottom: 3.5px solid transparent;
  }
  .letterhead-band {
    position: absolute; left: 0; right: 0; bottom: 0; height: 10px;
    background: linear-gradient(90deg, var(--brand-green) 70%, var(--swoosh-dark) 70%);
  }

  /* Envelopes */
  .envelope {
    position: absolute; left: 590px; width: 560px; height: 240px;
    background: var(--paper);
    box-shadow: 0 10px 24px rgba(0,0,0,0.25);
    overflow: hidden;
  }
  .envelope-back { top: 120px; }
  .envelope-front { top: 420px; }
  .envelope-flap { position: absolute; inset: 0; }
  .envelope-front .swooshes { position: absolute; inset: 0; }
  .envelope-front .brand-mark { position: absolute; left: 28px; top: 28px; }
  .envelope-front .brand-mark .brand-name { font-size: 15px; }
  .address-window {
    position: absolute; left: 28px; top: 108px;
    width: 230px; height: 88px;
    border: 1px solid var(--swoosh-dark); border-radius: 10px;
    background: #fbfcfb;
  }
  .envelope-contact {
    position: absolute; left: 0; right: 0; bottom: 12px;
    display: flex; justify-content: flex-end; gap: 18px; padding-right: 24px;
    font-size: 7.5px; color: var(--ink-soft);
  }
  .envelope-contact span { display: flex; align-items: center; gap: 4px; }
  .envelope-contact svg { width: 9px; height: 9px; fill: var(--brand-green); }
  .envelope-band {
    position: absolute; left: 0; right: 0; bottom: 30px; height: 4px;
    background: linear-gradient(90deg, var(--swoosh-dark) 35%, var(--brand-green) 35%);
  }
</style>
</head>
<body>

<section class="letterhead" aria-label="Letterhead">
  <svg class="swooshes" viewBox="0 0 460 650" preserveAspectRatio="none" aria-hidden="true">
    <path d="M0 230 C120 150 190 120 250 60 L460 60 L460 0 L0 0 Z" fill="var(--paper-shade)" opacity="0.5"/>
    <path d="M0 240 C140 160 210 110 250 55" fill="none" stroke="var(--swoosh)" stroke-width="6"/>
    <path d="M0 255 C150 175 220 125 265 60" fill="none" stroke="var(--swoosh)" stroke-width="3"/>
    <path d="M60 650 C200 560 300 520 460 470" fill="none" stroke="var(--swoosh)" stroke-width="8"/>
    <path d="M20 650 C180 580 300 500 400 380" fill="none" stroke="var(--swoosh)" stroke-width="4"/>
  </svg>

  <div class="letterhead-contact">
    <span class="brand-name">Bright Harbor Dental</span>
    Level 6, 1 Harbor Street, Denver CO 80202<br>
    (303) 555 0142 &nbsp;|&nbsp; (303) 555 0143 &nbsp;|&nbsp; hello@brightharbor.example<br>
    <span class="provider">Provider No. 0000000W &nbsp;|&nbsp; ABN 00 000 000 000</span>
  </div>

  <div class="brand-mark">
    <span class="brand-dot"></span>
    <span class="brand-name">Bright Harbor Dental</span>
  </div>

  <div class="services">
    <span class="services-title">Services:</span>
    <ul>
      <li>Bonding</li><li>Veneers</li><li>Dentures</li><li>Prosthodontics</li>
      <li>Restorations</li><li>Teeth Whitening</li><li>Cosmetic Dentistry</li>
      <li>Root Canal Therapy</li><li>Routine Tooth Extraction</li>
      <li>Cleanings &amp; Prevention, Exams</li>
    </ul>
  </div>
  <div class="letterhead-band"></div>
</section>

<section class="envelope envelope-back" aria-label="Envelope back">
  <svg class="envelope-flap" viewBox="0 0 560 240" preserveAspectRatio="none">
    <path d="M0 240 L0 0 L560 0 L560 110 Z" fill="var(--paper-shade)"/>
    <path d="M0 0 L560 0 L560 20 L60 150 Q20 160 0 130 Z" fill="var(--brand-green-dark)" role="img" aria-label="Green patterned envelope flap"/>
  </svg>
</section>

<section class="envelope envelope-front" aria-label="Envelope front">
  <svg class="swooshes" viewBox="0 0 560 240" preserveAspectRatio="none" aria-hidden="true">
    <path d="M180 240 C300 160 420 80 560 40" fill="none" stroke="var(--swoosh)" stroke-width="8"/>
    <path d="M240 240 C340 170 450 110 560 90" fill="none" stroke="var(--swoosh)" stroke-width="4"/>
  </svg>

  <div class="brand-mark">
    <span class="brand-dot"></span>
    <span class="brand-name">Bright Harbor Dental</span>
  </div>

  <div class="address-window"></div>
  <div class="envelope-band"></div>

  <div class="envelope-contact">
    <span><svg viewBox="0 0 10 10"><circle cx="5" cy="4" r="3"/><path d="M2.5 5.5 L5 10 L7.5 5.5Z"/></svg>1 Harbor St, Suite 6, Denver CO</span>
    <span><svg viewBox="0 0 10 10"><circle cx="5" cy="5" r="5"/></svg>(303) 555 0142</span>
    <span><svg viewBox="0 0 10 10"><rect x="0" y="2" width="10" height="6"/></svg>hello@brightharbor.example</span>
    <span><svg viewBox="0 0 10 10"><circle cx="5" cy="5" r="5"/></svg>brightharbor.example</span>
  </div>
</section>

</body>
</html>
```